Need a new company business card

I am looking for a new company business card. Front and back. With information on it as per below. Card should be professional. Yet clever. Simple. Modern design. Pim card, traditional size. OK with say, all black or all red backside.

Varnholt is an indie, bootstrapped magazine advancing the work of intersectional feminists busting their buts to create a just world through the power of enterprise and innovation.

Varnholt is the home and voice of entrepreneurial feminism and feminist innovators worldwide. Entrepreneurial feminists are people (of all genders) who see inequality as an innovation priority. They work to advance gender equity and/or who strive to integrate and practice feminist principles, pedagogy, values into their innovation and entrepreneurship work.
We are committed to this space being trans and queer inclusive, anti-racist, intersectional, brave, and safe. We welcome all allies. We value learning, edgy but civil discourse and integrative thinking skills.

Target Market(s)

feminists, business owners,

Industry/Entity Type

Publishing Company

Contact Information for Business Card

RD Tolliver
Founder/Publisher
4-237 Ashgrove Lane, Toronto, ON
M4T 2K8
publisher@varnholt.com
416-552-3019
www.varnholt.com

Font styles to use
Serif
Other font styles liked:
• Myriad Pro

Colors
ec1f27
000000
ffffff

Requirements
Must have
• logo
• use red, black white colours only.
Nice to have
• use the compass in pattern or creatively but not too busy please
Should not have
• Should not be too busy. Elegant.

```html
<!DOCTYPE html>
<html lang="en">
<head>
<meta charset="utf-8">
<title>Varnholt — Business Card</title>
<link rel="stylesheet" href="https://fonts.googleapis.com/css2?family=Roboto:ital,wght@0,400;0,500;0,700;1,700&family=PT+Serif:ital@0;1&display=swap">
<style>
  :root {
    --brand-red: #ec1f27;
    --ink: #2b2b2b;
    --ink-soft: #4a4a4a;
    --paper: #ffffff;
    --backdrop: #e4e4e4;
    --mark-light: #f0585e;
  }
  * { margin: 0; padding: 0; box-sizing: border-box; }
  html, body {
    width: 1200px; height: 960px; overflow: hidden;
    background: var(--backdrop);
    font-family: "Roboto", Arial, sans-serif;
  }
  .canvas { position: relative; width: 1200px; height: 960px; }

  .card { position: absolute; width: 601px; height: 343px; }
  .card-front { left: 314px; top: 113px; background: var(--paper); }
  .card-back { left: 311px; top: 472px; background: var(--brand-red); }

  .wordmark {
    position: absolute; left: 44px; top: 54px;
    font-family: "Roboto", Arial, sans-serif;
    font-weight: 700; font-size: 52px; line-height: 1;
    color: var(--ink); letter-spacing: -1px;
  }
  .cert-badge {
    position: absolute; left: 243px; top: 35px;
    width: 14px; height: 14px; border-radius: 50%;
    border: 1.5px solid var(--ink);
  }
  .tagline {
    position: absolute; left: 44px; top: 106px;
    display: flex; align-items: center; gap: 5px;
    font-family: "PT Serif", Georgia, serif;
    font-size: 8px; letter-spacing: 0.4px; color: var(--ink);
    white-space: nowrap;
  }
  .tagline .tag-square { width: 7px; height: 7px; background: var(--brand-red); }
  .tagline em { font-style: italic; color: var(--brand-red); }

  .person { position: absolute; left: 44px; top: 155px; }
  .person-name {
    font-size: 20px; font-weight: 500; color: var(--ink);
    text-transform: uppercase; letter-spacing: -0.2px; line-height: 24px;
  }
  .person-title { font-size: 15px; font-weight: 500; color: var(--brand-red); line-height: 18px; }

  .address {
    position: absolute; left: 44px; top: 204px;
    font-size: 14px; line-height: 19px; color: var(--ink-soft); font-style: normal;
  }
  .contacts { position: absolute; left: 44px; top: 249px; list-style: none; }
  .contacts li {
    display: flex; align-items: center; gap: 8px;
    font-size: 14px; line-height: 19.5px; color: var(--ink-soft);
  }
  .contacts svg { width: 13px; height: 13px; fill: var(--ink); flex: none; }

  .mark-area {
    position: absolute; left: 276px; top: 15px; width: 314px; height: 313px;
    border-radius: 14px;
    background: radial-gradient(circle at 50% 50%, var(--mark-light), var(--brand-red));
  }

  .back-pattern { position: absolute; inset: 0; background: var(--brand-red); }
  .back-url {
    position: absolute; left: 0; right: 0; top: 276px;
    display: flex; align-items: center; gap: 4px;
  }
  .back-url .rule { flex: 1; height: 1px; background: var(--paper); }
  .back-url span {
    font-weight: 700; font-style: italic; font-size: 18px;
    letter-spacing: 4.6px; color: var(--paper);
  }
</style>
</head>
<body>
<main class="canvas">
  <section class="card card-front" aria-label="Card front">
    <div class="wordmark">Varnholt</div>
    <div class="cert-badge" aria-hidden="true"></div>
    <div class="tagline"><span class="tag-square"></span><span>DISPATCHES <em>for</em> EQUITY-MINDED FOUNDERS</span></div>

    <div class="person">
      <p class="person-name">RD Tolliver</p>
      <p class="person-title">Founder/Publisher</p>
    </div>

    <address class="address">4-237 Ashgrove Lane<br>Toronto, ON, M4T 2K8</address>

    <ul class="contacts">
      <li><svg viewBox="0 0 24 24"><path d="M6.6 10.8a15 15 0 0 0 6.6 6.6l2.2-2.2c.3-.3.7-.4 1-.2 1.1.4 2.3.6 3.6.6.6 0 1 .4 1 1V20c0 .6-.4 1-1 1A17 17 0 0 1 3 4c0-.6.4-1 1-1h3.5c.6 0 1 .4 1 1 0 1.3.2 2.5.6 3.6.1.3 0 .7-.2 1z"/></svg>416-552-3019</li>
      <li><svg viewBox="0 0 24 24"><path d="M2 5h20v14H2z"/><path d="M3 6l9 7 9-7" fill="none" stroke="#fff" stroke-width="1.6"/></svg>publisher@varnholt.com</li>
      <li><svg viewBox="0 0 24 24"><circle cx="12" cy="12" r="10"/><path d="M2 12h20M12 2c3 3 3 17 0 20M12 2c-3 3-3 17 0 20" fill="none" stroke="#fff" stroke-width="1.4"/></svg>www.varnholt.com</li>
    </ul>

    <div class="mark-area" role="img" aria-label="Large brand symbol in red with a fine repeating pattern"></div>
  </section>

  <section class="card card-back" aria-label="Card back">
    <div class="back-pattern" role="img" aria-label="Red field with a fine repeating pattern"></div>
    <div class="back-url">
      <div class="rule"></div>
      <span>www.varnholt.com</span>
      <div class="rule"></div>
    </div>
  </section>
</main>
</body>
</html>
```